Letterhead for a German Distribution/Manufacturing Company

We need a professional Letterhead in a unique Design.
not to playful.
The Letterhead has to show show that we are a international company with headquater in Germany.
all details like adress, Vat Tax Number, Bank Accout, Eori, email, Company number has to be on the Letterhead.
for example use: VAT TAX DE5470318 Bank Account: Kestrel Bank IBAN DE412058731ß204683 Swift: MORV0417352 EORI 3150428697 Company Number: HRB 51806 Adress: VOLMINTA UG Ahornweg 7 Postal Code 06384 City Lindenfeld Country: Germany Email: info@volminta-example.com
the design can be colored but doesnt have to be
Industry/Entity Type
Manufacturing and international distribution
Requirements
Must have
- show that we are a international company with headquater in Germany. our company infos and logo

```html
<!DOCTYPE html>
<html lang="en">
<head>
<meta charset="utf-8">
<title>Volminta Letterhead</title>
<link href="https://fonts.googleapis.com/css2?family=Lato:wght@300;400;700&display=swap" rel="stylesheet">
<style>
  :root {
    --backdrop: #4e6079;
    --paper: #ffffff;
    --band: #545454;
    --band-text: #f2f2f2;
    --ink: #1e1e1e;
    --rule: #d9d9d9;
    --sign-tone: #ececec;
  }
  * { margin: 0; padding: 0; box-sizing: border-box; }
  html, body {
    width: 1200px; height: 725px; overflow: hidden;
    background: var(--backdrop);
    font-family: "Lato", sans-serif;
  }
  .letterhead {
    position: absolute; left: 343px; top: 12px;
    width: 513px; height: 700px;
    background: var(--paper);
    color: var(--ink);
  }
  .header-band {
    position: absolute; left: 0; top: 0;
    width: 100%; height: 125px;
    background: var(--band);
    color: var(--band-text);
  }
  .brand {
    position: absolute; left: 29px; top: 45px;
    display: flex; align-items: center; gap: 9px;
  }
  .brand-dot {
    width: 44px; height: 44px; border-radius: 50%;
    background: var(--band-text);
  }
  .brand-name {
    font-weight: 400; font-size: 27px; letter-spacing: 0.3px;
    color: var(--band-text);
  }
  .company-details {
    position: absolute; left: 247px; top: 27px;
    border-left: 1px solid var(--rule);
    padding-left: 7px;
    font-size: 8.2px; line-height: 11.6px;
    list-style: none;
  }
  .letter-body {
    position: absolute; left: 28px; top: 176px; width: 456px;
    font-size: 9.4px; line-height: 11px;
  }
  .letter-date { margin-bottom: 13px; }
  .recipient { margin-bottom: 12px; }
  .recipient-company { margin-bottom: 13px; }
  .salutation { font-size: 12px; font-weight: 700; margin-bottom: 12px; }
  .paragraph { text-align: justify; margin-bottom: 11px; }
  .closing { margin-top: 30px; }
  .signature {
    display: block; margin-top: 12px;
    width: 130px; height: 26px;
    background: var(--sign-tone);
  }
</style>
</head>
<body>
  <main class="letterhead">
    <header class="header-band">
      <div class="brand">
        <span class="brand-dot"></span>
        <span class="brand-name">VOLMINTA</span>
      </div>
      <ul class="company-details">
        <li>VAT TAX DE5470318</li>
        <li>Bank Account: Kestrel Bank IBAN DE412058731ß204683</li>
        <li>Swift: MORV0417352</li>
        <li>EORI 3150428697</li>
        <li>Company Number: HRB 51806</li>
        <li>Adress: VOLMINTA UG Ahornweg 7 Postal Code 06384</li>
        <li>City Lindenfeld Country</li>
        <li>Germany Email: info@volminta-example.com</li>
      </ul>
    </header>

    <section class="letter-body">
      <p class="letter-date">January-03-2020</p>
      <p class="recipient">Mr, Jonas Reiter<br>President</p>
      <p class="recipient-company">Harbor Works<br>123 Street Name, Suite# 10<br>City, State, 120023</p>
      <p class="salutation">Dear Mr, Jonas</p>
      <p class="paragraph">Lorem ipsum dolor sit amet, consectetur adipisicing elit, sed do eiusmod tempor incididunt ut labore et dolore magna aliqua. Ut enim ad minim veniam, quis nostrud exercitation ullamco laboris nisi ut aliquip ex ea commodo consequat. Duis aute irure dolor in reprehenderit in voluptate velit esse cillum dolore eu fugiat nulla pariatur.</p>
      <p class="paragraph">Lorem ipsum dolor sit amet, consectetur adipisicing elit, sed do eiusmod tempor incididunt ut labore et dolore magna aliqua. Ut enim ad minim veniam, quis nostrud exercitation ullamco laboris nisi ut aliquip ex ea commodo consequat. Duis aute irure dolor in reprehenderit in voluptate velit esse cillum dolore eu fugiat nulla pariatur.</p>
      <p class="paragraph">Lorem ipsum dolor sit amet, consectetur adipisicing elit, sed do eiusmod tempor incididunt ut labore et dolore magna aliqua. Ut enim ad minim veniam, quis nostrud exercitation ullamco laboris nisi ut aliquip ex ea commodo consequat.</p>
      <p class="paragraph">Excepteur sint occaecat cupidatat non proident, sunt in culpa qui officia deserunt mollit anim id est laborum. re et dolore magnam aliquam quaerat voluptatem.</p>
      <p class="closing">Regards</p>
      <span class="signature" role="img" aria-label="Handwritten signature of Martin Keller"></span>
    </section>
  </main>
</body>
</html>
```